Realtor branding business card

modern, simple and self branding. Broker office logo needs to be used but not emphasized. Looking to brand myself

Target Market(s)

buyers, sellers and investors

Industry/Entity Type

Realtor

Contact Information for Business Card

Sample of my current business card on file

Requirements
Must have
• my website - tobiasmerrowkl.com
• Realtor logo
• Fair housing logo
Nice to have
• Colors from office logo but not a must
Should not have
• Do not want headshot

```html
<!DOCTYPE html>
<html lang="en">
<head>
<meta charset="utf-8">
<title>Tobias Merrow – Realtor Business Card</title>
<link href="https://fonts.googleapis.com/css2?family=Oswald:wght@500;700&family=Lato:wght@400;700&display=swap" rel="stylesheet">
<style>
  :root {
    --backdrop: #e8e4dc;
    --card-black: #0b0b0c;
    --card-purple: #4f4c8a;
    --brand-indigo: #3a3791;
    --accent-red: #c8262c;
    --accent-blue: #2f62b8;
    --text-light: #f2f2f2;
    --skyline-tone: #1d1d20;
  }
  * { box-sizing: border-box; margin: 0; padding: 0; }
  html, body {
    width: 1200px; height: 1200px; overflow: hidden;
    background: var(--backdrop);
  }
  .sheet {
    width: 1200px; height: 1200px;
    display: flex; flex-direction: column; align-items: center; justify-content: center;
    gap: 44px;
  }
  .card {
    position: relative; width: 900px; height: 514px; overflow: hidden;
    box-shadow: 0 6px 18px rgba(0,0,0,0.18);
  }

  /* Back side */
  .card--back { background: var(--card-purple); }
  .card--back .brand-mark {
    position: absolute; left: 0; right: 0; top: 186px;
    text-align: center; color: #fff;
    font-family: "Oswald", sans-serif; font-weight: 700;
    font-size: 60px; line-height: 1; letter-spacing: 1px; text-transform: uppercase;
  }
  .card--back .brand-mark .sub {
    display: block; font-size: 32px; margin-top: 12px; letter-spacing: 4px;
  }
  .card--back .web {
    position: absolute; right: 60px; bottom: 40px;
    font-family: "Lato", sans-serif; font-size: 24px; color: #fff;
  }
  .card--back .web .domain { color: var(--accent-red); font-weight: 700; }

  /* Front side */
  .card--front { background: var(--card-black); }
  .skyline {
    position: absolute; left: 0; right: 0; bottom: 0; height: 340px;
    background: linear-gradient(180deg, rgba(29,29,32,0) 0%, var(--skyline-tone) 45%, var(--skyline-tone) 100%);
  }
  .front-brand {
    position: absolute; left: 70px; top: 48px;
    font-family: "Oswald", sans-serif; font-weight: 700; color: var(--brand-indigo);
    text-transform: uppercase; line-height: 1;
    display: flex; align-items: flex-start; gap: 12px;
  }
  .front-brand .square { width: 18px; height: 18px; background: var(--brand-indigo); margin-top: 12px; }
  .front-brand .name { font-size: 44px; }
  .front-brand .name .sub { display: block; font-size: 25px; margin-top: 6px; letter-spacing: 3px; }

  .agent {
    position: absolute; left: 70px; top: 250px;
  }
  .agent .agent-name {
    font-family: "Oswald", sans-serif; font-weight: 500; font-size: 40px; line-height: 1.1;
    color: var(--text-light); text-transform: uppercase; letter-spacing: 0.5px;
  }
  .agent .role {
    font-family: "Lato", sans-serif; font-size: 24px; line-height: 1.2; color: var(--accent-blue);
  }
  .rule {
    position: absolute; left: 160px; right: 70px; top: 329px;
    height: 2px; background: var(--accent-red);
  }
  .contacts {
    position: absolute; left: 70px; top: 346px; list-style: none;
    font-family: "Lato", sans-serif; font-size: 21px; color: var(--text-light);
  }
  .contacts li { display: flex; align-items: center; gap: 12px; height: 31px; }
  .contacts svg { width: 18px; height: 18px; fill: var(--accent-blue); flex: none; }
  .contacts .label { width: 70px; }
  .contacts .site { font-weight: 700; }

  .badges {
    position: absolute; right: 70px; top: 352px; display: flex; gap: 8px;
  }
  .badges span { width: 30px; height: 30px; background: #fff; display: block; }

  .address {
    position: absolute; right: 70px; bottom: 40px; text-align: right;
    font-family: "Lato", sans-serif; font-size: 24px; line-height: 1.3; color: var(--text-light);
  }
</style>
</head>
<body>
<main class="sheet">

  <section class="card card--back" aria-label="Card back">
    <div class="brand-mark">Keel Harbor<span class="sub">Realty Group</span></div>
    <p class="web">www.<span class="domain">tobiasmerrowkl</span>.com</p>
  </section>

  <section class="card card--front" aria-label="Card front">
    <div class="skyline" role="img" aria-label="Faint dark city skyline silhouette"></div>

    <div class="front-brand">
      <span class="square"></span>
      <span class="name">Keel Harbor<span class="sub">Realty Group</span></span>
    </div>

    <div class="agent">
      <h1 class="agent-name">Tobias Merrow</h1>
      <p class="role">Realtor</p>
    </div>
    <div class="rule"></div>

    <ul class="contacts">
      <li>
        <svg viewBox="0 0 24 24" aria-hidden="true"><path d="M6.6 10.8a15 15 0 0 0 6.6 6.6l2.2-2.2a1 1 0 0 1 1-.25 11.4 11.4 0 0 0 3.6.57 1 1 0 0 1 1 1V20a1 1 0 0 1-1 1A17 17 0 0 1 3 4a1 1 0 0 1 1-1h3.5a1 1 0 0 1 1 1c0 1.25.2 2.45.57 3.57a1 1 0 0 1-.25 1z"/></svg>
        <span class="label">Cell:</span><span>+407 - 555 - 0148</span>
      </li>
      <li>
        <svg viewBox="0 0 24 24" aria-hidden="true"><path d="M2 9c0-3 4.5-5 10-5s10 2 10 5v2h-5V9H7v2H2z M5 13h14l2 7H3z"/></svg>
        <span class="label">Office:</span><span>+407 - 555 - 0190</span>
      </li>
      <li>
        <svg viewBox="0 0 24 24" aria-hidden="true"><path d="M2 5h20v14H2z M3 6l9 7 9-7" stroke="#0b0b0c" stroke-width="1.5"/></svg>
        <span>tmerrow@tobiasmerrowkl.com</span>
      </li>
      <li>
        <svg viewBox="0 0 24 24" aria-hidden="true"><circle cx="12" cy="12" r="10"/><path d="M2 12h20M12 2c3 3 3 17 0 20M12 2c-3 3-3 17 0 20" stroke="#0b0b0c" stroke-width="1.3" fill="none"/></svg>
        <span class="site">www.tobiasmerrowkl.com</span>
      </li>
    </ul>

    <div class="badges" aria-label="Realtor and fair housing badges">
      <span></span><span></span>
    </div>

    <p class="address">480 Larkspur Ridge Rd<br>Maple Hollow, FL 32790</p>
  </section>

</main>
</body>
</html>
```